Business Card Design Project

We are not a new company, but renamed to "Vantorin Kitchens" last year. We specialize in modern high-end cabinetry imports. We would like to communicate a sense of quality and cutting edge technology. Ideally the design would incorporate our logo colors, silver, red and preferably a black, matte background. Though we are open to suggestions.
Logo is attached.
Edit: I have attached rough drafts of the previous cards, this way you will have all necessary content that needs to go on the cards.
Updates
Project Deadline Extended
Reason: We have received a lot of great designs, but due to the sheer number we couldn't respond to all. We will extend the deadline for another 7 days to finalize and provide feedback to designers.
Thank you for your hard work!
Industry/Entity Type
Business
Look and feel
Each slider illustrates characteristics of the customer's brand and the style your logo design should communicate.

```html
<!DOCTYPE html>
<html lang="en">
<head>
<meta charset="UTF-8">
<title>Vantorin Kitchens – Business Cards</title>
<link href="https://fonts.googleapis.com/css2?family=Arimo:wght@400;700&display=swap" rel="stylesheet">
<style>
  :root {
    --matte-black: #0b0b0b;
    --silver: #c8c8c8;
    --silver-dark: #9a9a9a;
    --brand-red: #e3202a;
    --ink-white: #f4f4f4;
    --backdrop: #e9e9ec;
  }
  * { box-sizing: border-box; margin: 0; padding: 0; }
  html, body {
    width: 1200px; height: 987px; overflow: hidden;
    background: var(--backdrop);
    font-family: 'Arimo', Arial, sans-serif;
  }
  .sheet {
    width: 1200px; height: 987px;
    display: flex; flex-direction: column;
    align-items: center; justify-content: center; gap: 40px;
  }
  .card {
    position: relative;
    width: 780px; height: 446px;
    border-radius: 26px;
    overflow: hidden;
    background: var(--matte-black);
  }
  .card-art { position: absolute; inset: 0; }

  .wordmark {
    display: flex; align-items: center; gap: 12px;
    color: var(--silver);
    font-weight: 700;
    text-transform: uppercase;
    letter-spacing: 1px;
    white-space: nowrap;
  }
  .wordmark-square { background: var(--silver); flex: none; }

  /* Front */
  .front .wordmark {
    position: absolute; left: 40px; top: 140px;
    font-size: 24px;
  }
  .front .wordmark-square { width: 20px; height: 20px; }

  .contact-list {
    position: absolute; left: 40px; top: 196px;
    list-style: none;
    color: var(--ink-white);
    font-size: 16px; line-height: 30px;
  }
  .contact-list li { display: flex; align-items: center; gap: 10px; }
  .contact-icon { width: 14px; height: 14px; flex: none; }

  .divider {
    position: absolute; left: 270px; top: 336px;
    width: 1px; height: 70px;
    background: var(--silver-dark);
  }
  .address {
    position: absolute; left: 288px; top: 342px;
    color: var(--ink-white);
    font-size: 16px; line-height: 28px;
    font-style: normal;
  }

  .person {
    position: absolute; right: 44px; top: 150px;
    text-align: right;
  }
  .person-name {
    color: var(--ink-white);
    font-size: 26px; font-weight: 700; letter-spacing: 1px;
    text-transform: uppercase;
  }
  .person-title {
    color: var(--brand-red);
    font-size: 21px; font-weight: 700;
  }

  /* Back */
  .back { display: flex; align-items: center; justify-content: center; }
  .back .wordmark { font-size: 46px; gap: 14px; letter-spacing: 2px; }
  .back .wordmark-square { width: 34px; height: 34px; }
</style>
</head>
<body>
<main class="sheet">

  <section class="card front" aria-label="Card front">
    <svg class="card-art" viewBox="0 0 780 446" aria-hidden="true">
      <defs>
        <linearGradient id="silverPanel" x1="0" y1="0" x2="1" y2="1">
          <stop offset="0" stop-color="#e6e6e6"/>
          <stop offset="0.55" stop-color="#bdbdbd"/>
          <stop offset="1" stop-color="#9c9c9c"/>
        </linearGradient>
      </defs>
      <path d="M120,0 C420,30 560,250 660,446 L780,446 L780,0 Z" fill="url(#silverPanel)"/>
      <path d="M110,0 C410,34 548,250 646,446 L630,446 C530,256 392,42 92,0 Z" fill="#0b0b0b"/>
      <path d="M98,0 C398,36 536,252 632,446 L612,446 C512,262 376,46 74,0 Z" fill="#e3202a"/>
    </svg>

    <div class="wordmark"><span class="wordmark-square"></span>Vantorin Kitchens</div>

    <ul class="contact-list">
      <li>
        <svg class="contact-icon" viewBox="0 0 14 14" aria-hidden="true"><path d="M3 1 L5.5 1 L6.5 4 L5 5.2 C5.8 7 7 8.2 8.8 9 L10 7.5 L13 8.5 L13 11 C13 12 12 13 11 13 C5.5 12.6 1.4 8.5 1 3 C1 2 2 1 3 1 Z" fill="#e3202a"/></svg>
        780.555.0142
      </li>
      <li>
        <svg class="contact-icon" viewBox="0 0 14 14" aria-hidden="true"><rect x="1" y="5" width="12" height="7" rx="1" fill="#e3202a"/><rect x="3" y="1.5" width="8" height="4" fill="none" stroke="#e3202a" stroke-width="1.5"/></svg>
        780.555.0187
      </li>
      <li>
        <svg class="contact-icon" viewBox="0 0 14 14" aria-hidden="true"><rect x="3.5" y="1" width="7" height="12" rx="1.5" fill="none" stroke="#e3202a" stroke-width="1.5"/><circle cx="7" cy="10.5" r="1" fill="#e3202a"/></svg>
        780.555.0163
      </li>
      <li>
        <svg class="contact-icon" viewBox="0 0 14 14" aria-hidden="true"><rect x="1" y="3" width="12" height="8.5" rx="1" fill="#e3202a"/><path d="M1.5 3.5 L7 8 L12.5 3.5" fill="none" stroke="#0b0b0b" stroke-width="1.2"/></svg>
        marcus@vantorinkitchens.ca
      </li>
    </ul>

    <div class="divider"></div>
    <address class="address">2816 - 41 Ave.<br>Ridgeford, AB T4N 2P8</address>

    <div class="person">
      <p class="person-name">Marcus Delane</p>
      <p class="person-title">Director</p>
    </div>
  </section>

  <section class="card back" aria-label="Card back">
    <div class="wordmark"><span class="wordmark-square"></span>Vantorin Kitchens</div>
  </section>

</main>
</body>
</html>
```